interior designer/stylist looking for a letter press business card to reflect the stylish work

Hello Designers,
I need a business card design for an company called Mosaic Interior Design. I'm aiming at the high end residential and private client market in London providing sleek simple interiors. I'd like my business card to be pinterest worthy and expensive looking, i want people to pin it and for it to have a sought after look, and want prospective customers to hire me as their interior designer as my card is so beautiful.
I love letter press design. I also like the use of colour/foil on the edge.
Colour combos & general things I like -
Black and White
Navy Blue and Gold
Neutral colours (muted palette of greys whites navys beiges)
White Marble & brass
Vorelle (fashion designer)
....also open to other suggestions....
Please dont take the pink in the attached photos too literally. i'd like the card to look more masculine than feminine.
I'd like Mosaic on one side in one font, with interior design underneath so one word will make the statement....... unless anyone has any other ideas, open to suggestions.
I'd like a really simple font and for the whole card to look very graphic.
my details -
Petra Wendlecombe
Interior Designer & Stylist
email petra@mosaicinteriordesign.co.uk
phone +447311584209
website wwww.mosaicinteriordesign.co.uk
GO GO GO!! EXCITED TO SEE THE OUTCOME!!
x P
Target Market(s)
High End Residential and private clients
Industry/Entity Type
Business
Contact Information for Business Card
Mosaic Interior Design & Styling
Petra Wendlecombe
phone +447311584209

```html
<!DOCTYPE html>
<html lang="en">
<head>
<meta charset="utf-8">
<title>Mosaic Interior Design — Business Card Concepts</title>
<link rel="stylesheet" href="https://fonts.googleapis.com/css2?family=Nunito+Sans:wght@300;400;600&family=EB+Garamond:wght@500&display=swap">
<style>
  :root {
    --paper: #ffffff;
    --ink: #141414;
    --card-black: #0b0b0b;
    --card-charcoal: #262626;
    --grey-mid: #7a7a7a;
    --grey-soft: #bdbdbd;
    --grey-light: #d2d2d2;
    --foil-edge: #8a7b4e;
    --sans: "Nunito Sans", "Helvetica Neue", Arial, sans-serif;
    --serif: "EB Garamond", Georgia, serif;
  }
  * { box-sizing: border-box; margin: 0; padding: 0; }
  html, body { width: 1200px; height: 861px; overflow: hidden; background: var(--paper); }
  .sheet { position: relative; width: 1200px; height: 861px; background: var(--paper); }

  .card {
    position: absolute;
    width: 346px; height: 224px;
    border: 1.5px solid var(--foil-edge);
    border-radius: 12px;
    overflow: hidden;
    background: var(--paper);
    font-family: var(--sans);
    color: var(--ink);
  }
  .card--black { background: var(--card-black); color: #fff; }
  .card--charcoal { background: var(--card-charcoal); color: #fff; }

  .pattern { position: absolute; inset: 0; }

  .studio-name {
    position: absolute;
    left: 0; right: 0;
    text-align: center;
    font-family: var(--sans);
    font-weight: 400;
    font-size: 25px;
    letter-spacing: 0.4px;
    white-space: nowrap;
  }
  .studio-name--ink { color: var(--ink); }
  .studio-name--grey { color: var(--grey-mid); }
  .studio-name--light { color: var(--grey-light); }
  .studio-name--serif { font-family: var(--serif); font-weight: 500; font-size: 27px; }
  .studio-name--left { left: 30px; right: auto; text-align: left; }

  .holder-name { position: absolute; text-transform: uppercase; font-weight: 400; letter-spacing: 0.6px; white-space: nowrap; }
  .holder-role { position: absolute; font-weight: 400; letter-spacing: 0.6px; white-space: nowrap; }
  .rule { position: absolute; height: 1px; background: var(--grey-soft); }

  .contacts { position: absolute; list-style: none; }
  .contacts li { white-space: nowrap; }
  .contacts .key { display: inline-block; }

  .url { position: absolute; left: 0; right: 0; text-align: center; font-size: 11px; color: var(--ink); }
</style>
</head>
<body>
<main class="sheet">

  <!-- Front, white, sans -->
  <section class="card" style="left:53px; top:38px;">
    <p class="studio-name studio-name--ink" style="top:94px;">Mosaic Interior Design</p>
  </section>

  <!-- Front, black, with name -->
  <section class="card card--black" style="left:422px; top:38px;">
    <p class="studio-name studio-name--grey studio-name--left" style="top:40px;">Mosaic Interior Design</p>
    <p class="holder-name" style="left:30px; top:168px; font-size:15px; color:#fff;">Petra Wendlecombe</p>
    <p class="holder-role" style="left:30px; top:190px; font-size:10.5px; color:var(--grey-soft);">Interior Designer &amp; Stylist</p>
  </section>

  <!-- Front, white, serif -->
  <section class="card" style="left:790px; top:37px;">
    <p class="studio-name studio-name--serif studio-name--ink" style="top:92px;">Mosaic Interior Design</p>
  </section>

  <!-- Back, black, full details -->
  <section class="card card--black" style="left:56px; top:289px;">
    <p class="holder-name" style="left:27px; top:32px; font-size:23px; font-weight:300; color:var(--grey-soft);">Petra Wendlecombe</p>
    <p class="holder-role" style="left:27px; top:63px; font-size:12.5px; color:#fff;">Interior Designer &amp; Stylist</p>
    <div class="rule" style="left:27px; top:89px; width:215px;"></div>
    <ul class="contacts" style="left:27px; top:148px; font-size:11.5px; line-height:17.5px; color:#fff;">
      <li><span class="key" style="width:17px; color:var(--grey-soft)">e</span>petra@mosaicinteriordesign.co.uk</li>
      <li><span class="key" style="width:17px; color:var(--grey-soft)">t</span>+44 (0)731 158 4209</li>
      <li><span class="key" style="width:17px; color:var(--grey-soft)">w</span>www.mosaicinteriordesign.co.uk</li>
    </ul>
  </section>

  <!-- Back, white with faint texture -->
  <section class="card" style="left:426px; top:289px;">
    <div class="pattern" role="img" aria-label="Faint repeating rows of the studio name as a background texture"
         style="background:linear-gradient(180deg,#f3f3f3,#ebebeb);"></div>
    <ul class="contacts" style="left:26px; top:144px; font-size:14px; line-height:21px; color:var(--ink);">
      <li><span class="key" style="width:12px; font-weight:600">e</span>petra@mosaicinteriordesign.co.uk</li>
      <li><span class="key" style="width:12px; font-weight:600">t</span>+44 (0)731 158 4209</li>
      <li>www.mosaicinteriordesign.co.uk</li>
    </ul>
  </section>

  <!-- Back, white, serif details -->
  <section class="card" style="left:796px; top:286px; width:340px; height:220px;">
    <ul class="contacts" style="left:26px; top:140px; font-family:var(--serif); font-weight:500; font-size:14px; line-height:21px; color:var(--ink);">
      <li>e petra@mosaicinteriordesign.co.uk</li>
      <li>t +44 (0)731 158 4209</li>
      <li>www.mosaicinteriordesign.co.uk</li>
    </ul>
  </section>

  <!-- Front, white with texture -->
  <section class="card" style="left:44px; top:550px; width:347px; height:226px;">
    <div class="pattern" role="img" aria-label="Faint repeating rows of the studio name as a background texture"
         style="background:linear-gradient(180deg,#f4f4f4,#ececec);"></div>
    <p class="studio-name studio-name--ink" style="top:90px;">Mosaic Interior Design</p>
    <p class="url" style="top:128px;">www.mosaicinteriordesign.co.uk</p>
  </section>

  <!-- Front, charcoal with texture -->
  <section class="card card--charcoal" style="left:434px; top:554px; width:347px; height:225px;">
    <div class="pattern" role="img" aria-label="Dark repeating rows of the studio name as a background texture"
         style="background:linear-gradient(180deg,#2b2b2b,#1f1f1f);"></div>
    <p class="studio-name studio-name--light" style="top:96px;">Mosaic Interior Design</p>
  </section>

</main>
</body>
</html>
```